Corporate Business Card

Very professional, Modern, Not to busy, include phone address email, website
(253) 617-4930, 18761 52nd Avenue S, Kent, WA 98047, martin@plumlinegroup.com, varkoworks.com

Target Market(s)

Manufacturing

Industry/Entity Type

Aero, machining, manufacturing, Off road racing

Contact Information for Business Card

Phone, address email, website

```html
<!DOCTYPE html>
<html lang="en">
<head>
<meta charset="utf-8">
<title>Varko Works – Business Card</title>
<link href="https://fonts.googleapis.com/css2?family=Montserrat:wght@500;600;700;800&display=swap" rel="stylesheet">
<style>
  :root {
    --navy: #16346e;
    --red: #d2232a;
    --white: #ffffff;
    --ink: #1c1c1c;
    --backdrop: #3b3b3d;
  }
  * { margin: 0; padding: 0; box-sizing: border-box; }
  html, body { width: 1200px; height: 904px; overflow: hidden; }
  body {
    background: var(--backdrop);
    font-family: "Montserrat", sans-serif;
    position: relative;
  }
  .card {
    position: absolute;
    left: 250px;
    width: 700px;
    height: 400px;
    overflow: hidden;
    box-shadow: 0 10px 24px rgba(0,0,0,.45);
  }
  .card--front { top: 32px; background: var(--navy); }
  .card--back  { top: 472px; background: var(--white); }

  .brand { position: absolute; display: flex; align-items: center; gap: 12px; }
  .brand__mark { width: 20px; height: 20px; background: var(--red); flex: none; }
  .brand__name {
    font-weight: 800;
    letter-spacing: 1px;
    white-space: nowrap;
  }
  .brand__rule { position: absolute; height: 2px; }

  .card--front .brand { left: 120px; top: 150px; }
  .card--front .brand__name { color: var(--white); font-size: 56px; }
  .card--front .brand__rule { left: 120px; top: 248px; width: 250px; background: var(--white); }

  .card--back .brand { right: 40px; top: 44px; }
  .card--back .brand__name { color: var(--navy); font-size: 36px; }
  .card--back .brand__rule { left: 340px; top: 112px; width: 170px; background: var(--navy); }

  .wave { position: absolute; inset: 0; }

  .address {
    position: absolute; left: 56px; top: 136px;
    font-size: 17px; font-weight: 500; color: var(--ink); line-height: 1.35;
  }
  .contacts {
    position: absolute; left: 56px; top: 212px;
    list-style: none; font-size: 16px; font-weight: 500; color: var(--ink);
  }
  .contacts li { display: flex; align-items: center; gap: 10px; height: 26px; }
  .contacts svg { width: 16px; height: 16px; fill: var(--red); flex: none; }
</style>
</head>
<body>

<section class="card card--front">
  <div class="brand">
    <span class="brand__mark"></span>
    <span class="brand__name">VARKO WORKS</span>
  </div>
  <span class="brand__rule"></span>
</section>

<section class="card card--back">
  <div class="brand">
    <span class="brand__mark"></span>
    <span class="brand__name">VARKO WORKS</span>
  </div>
  <span class="brand__rule"></span>

  <p class="address">18761 52nd Avenue<br>S, Kent, WA 98047</p>

  <ul class="contacts">
    <li>
      <svg viewBox="0 0 24 24" aria-hidden="true"><path d="M6.6 10.8a15 15 0 0 0 6.6 6.6l2.2-2.2c.3-.3.7-.4 1-.2 1.1.4 2.3.6 3.6.6.6 0 1 .4 1 1V20c0 .6-.4 1-1 1A17 17 0 0 1 3 4c0-.6.4-1 1-1h3.5c.6 0 1 .4 1 1 0 1.3.2 2.5.6 3.6.1.3 0 .7-.2 1z"/></svg>
      (253) 617-4930
    </li>
    <li>
      <svg viewBox="0 0 24 24" aria-hidden="true"><path d="M2 5h20v14H2z M2 5l10 8 10-8" stroke="#fff" stroke-width="1.5"/></svg>
      martin@plumlinegroup.com
    </li>
    <li>
      <svg viewBox="0 0 24 24" aria-hidden="true"><circle cx="12" cy="12" r="10"/><path d="M2 12h20M12 2c3 3 3 17 0 20M12 2c-3 3-3 17 0 20" stroke="#fff" stroke-width="1.3" fill="none"/></svg>
      www.varkoworks.com
    </li>
  </ul>

  <svg class="wave" viewBox="0 0 700 400" aria-hidden="true">
    <path d="M0,400 L0,366 C220,366 340,342 450,264 S630,164 700,158 L700,400 Z" fill="var(--navy)"/>
    <path d="M0,348 C220,348 332,324 442,246 S620,146 690,140" fill="none" stroke="var(--red)" stroke-width="14"/>
  </svg>
</section>

</body>
</html>
```